PlayTallyCollective - Game Statistics and Achievement Tracking

I need a new modern design for an existing website.

The website is a project to track statistics and achievements for games (currently Vaporn Achievements/Stats and stats for Cargo Haul Odyssey 2 and Frontier Rig Journeys).
I am currently expanding the site with other platforms (like QVR) and more games.
I am also adding a user registration/signin with user profiles to show off their achievements and stats across all platforms and games.

The current website is available at https://plytly.example/
To search for data you can use the username "pixelornin" (without quotes).

The design should be modern and extendable and contain space for a logo.

The logo should match the project. It should combine Gaming with statistics.

Target Market(s)

Video game players

Number of Pages Required

5+ page

Font styles to use
Sans Serif

Requirements
Must have
• Basic Layout, User profile page (not yet available on live site), Search Page for Platforms/Games, Platform profile page, Dark theme

```html
<!DOCTYPE html>
<html lang="en">
<head>
<meta charset="utf-8">
<title>PlayTallyCollective – Screens</title>
<link href="https://fonts.googleapis.com/css2?family=Open+Sans:wght@400;600;700&display=swap" rel="stylesheet">
<style>
:root{
  --page-bg:#0c1a1f;
  --panel-bg:#0b0c0f;
  --bar-bg:#111216;
  --card-bg:rgba(17,18,22,.92);
  --card-line:#2a2d33;
  --text:#f2f3f5;
  --muted:#9a9ea6;
  --dim:#6c7078;
  --accent:#1ea8e0;
  --green:#3fd83f;
  --green-dark:#27b727;
  --gold:#e8b93a;
  --violet:#8f5ad8;
}
*{box-sizing:border-box;margin:0;padding:0}
html,body{width:1200px;height:2662px;overflow:hidden}
body{
  font-family:"Open Sans",sans-serif;color:var(--text);position:relative;
  background:
    radial-gradient(ellipse 600px 500px at 1100px 500px,#1d4650 0%,transparent 70%),
    radial-gradient(ellipse 500px 700px at 80px 1900px,#1b3d47 0%,transparent 70%),
    radial-gradient(ellipse 500px 400px at 900px 2400px,#17353c 0%,transparent 70%),
    linear-gradient(180deg,#0e1519 0%,#10262c 40%,#0f2228 70%,#0d1a1f 100%);
}
.panel{position:absolute;left:136px;width:928px;height:522px;background:var(--panel-bg);overflow:hidden;box-shadow:0 10px 40px rgba(0,0,0,.6)}
.scene{position:absolute;left:0;right:0;top:58px;bottom:27px}
.topbar{position:absolute;left:0;top:0;width:100%;height:58px;background:linear-gradient(180deg,#16171b,#0e0f12);border-bottom:1px solid #1d1f24;z-index:3}
.brand{position:absolute;left:29px;top:20px;display:flex;align-items:center;gap:6px}
.brand-dot{width:16px;height:16px;border-radius:50%;background:var(--gold)}
.brand-name{font-size:10px;font-weight:600;color:var(--accent)}
.nav{position:absolute;top:0;height:58px}
.nav-item{position:absolute;top:22px;display:flex;align-items:center;gap:6px;font-size:8px;color:var(--muted);white-space:nowrap}
.nav-item.active{color:var(--text)}
.nav-item svg{width:10px;height:10px}
.nav-dot{width:10px;height:10px;border-radius:50%;background:#c9d6e2}
.nav-dot.games{background:var(--gold)}
.nav-line{position:absolute;bottom:0;height:3px;width:60px;background:var(--accent);border-radius:2px 2px 0 0}
.user-chip{position:absolute;right:14px;top:22px;display:flex;align-items:center;gap:5px;font-size:8px;font-weight:600}
.user-chip .face{width:14px;height:14px;border-radius:50%;background:linear-gradient(135deg,#7ec9e6,#c69356)}
.footbar{position:absolute;left:0;bottom:0;width:100%;height:27px;background:#000;font-size:7.5px;color:#d7d9dc;z-index:3}
.footbar span{position:absolute;top:9px}
.footbar .ver{left:12px}.footbar .copy{left:50%;transform:translateX(-50%)}.footbar .imp{right:15px}
.art{position:absolute}
.card{position:absolute;background:var(--card-bg);border:1px solid var(--card-line);border-radius:12px}
.rule{height:1px;background:#3a3d44}
.icon{width:9px;height:9px;stroke:currentColor;fill:none;stroke-width:1.6}

/* panel 1 */
.hero-card{left:116px;top:128px;width:696px;height:293px;background:rgba(14,15,19,.88)}
.hero-title{position:absolute;left:28px;top:28px;font-size:28px;font-weight:700}
.hero-card .rule{position:absolute;left:28px;right:40px;top:78px}
.hero-sub{position:absolute;left:28px;top:108px;font-size:14px;font-weight:700}
.hero-text{position:absolute;left:28px;top:145px;font-size:9.5px;line-height:28px;color:#e4e6ea}
.hero-text a{color:var(--accent)}

/* panel 2 */
.profile-card{left:97px;top:89px;width:171px;height:381px}
.tool-row{position:absolute;left:37px;top:12px;display:flex;gap:13px;color:var(--muted)}
.tool-row svg{width:11px;height:11px}
.avatar{position:absolute;border-radius:50%;background:radial-gradient(circle at 50% 40%,#6fc6e8 0%,#3b8bbd 55%,#23407a 100%);border:3px solid #e8eef5}
.profile-card .avatar{left:33px;top:39px;width:104px;height:104px}
.pname{position:absolute;width:100%;text-align:center;font-size:11px;font-weight:600}
.profile-card .pname{top:153px}
.badges{position:absolute;top:175px;left:0;width:100%;display:flex;justify-content:center;gap:17px}
.badge{width:19px;height:19px;font-size:6.5px;display:flex;align-items:center;justify-content:center;position:relative}
.badge svg{position:absolute;inset:0;width:19px;height:19px;fill:none;stroke-width:1.3}
.profile-card .rule{position:absolute;left:14px;right:14px;top:208px}
.pstat{position:absolute;left:14px;font-size:7px;display:flex;width:150px}
.pstat .lab{width:72px;color:var(--text)}
.pstat .val{display:flex;align-items:center;gap:5px;color:var(--dim)}
.stats-bar{left:279px;top:89px;width:551px;height:52px}
.stats-bar h2{position:absolute;left:19px;top:18px;font-size:11px;font-weight:600}
.stats-bar .plus{position:absolute;right:18px;top:17px;width:16px;height:16px;stroke:var(--text);stroke-width:1.4}
.games-card{left:279px;top:158px;width:551px;height:312px;overflow:hidden}
.search-pill{position:absolute;left:19px;top:15px;width:118px;height:21px;border-radius:11px;background:#1a1c21;font-size:7.5px;color:var(--dim);display:flex;align-items:center;gap:5px;padding-left:8px}
.select-pill{position:absolute;left:362px;top:15px;width:118px;height:21px;border-radius:11px;background:#1a1c21;font-size:7.5px;color:var(--dim);display:flex;align-items:center;justify-content:space-between;padding:0 8px}
.round-btn{position:absolute;top:15px;width:21px;height:21px;border-radius:50%;background:#1a1c21;color:var(--muted);display:flex;align-items:center;justify-content:center}
.games-card .rule{position:absolute;left:19px;right:19px;top:48px}
.tile{position:absolute;width:165px}
.cover{height:50px;border-radius:5px}
.tile-meta{display:flex;justify-content:space-between;margin-top:10px;font-size:8px;font-weight:700}
.tile-meta .nums{display:flex;gap:9px;font-weight:400}
.tile-meta .nums span{display:flex;align-items:center;gap:2px}
.bar{margin-top:4px;height:11px;border-radius:6px;background:repeating-linear-gradient(135deg,var(--green) 0 6px,var(--green-dark) 6px 12px);font-size:6.5px;font-weight:700;text-align:right;padding-right:8px;line-height:11px}
.games-card .fade{position:absolute;left:0;right:0;bottom:0;height:30px;background:linear-gradient(180deg,transparent,rgba(17,18,22,.9))}

/* panel 3 */
.search-card{left:189px;top:186px;width:550px;height:145px;background:rgba(20,21,25,.9)}
.search-card h2{position:absolute;left:19px;top:16px;font-size:20px;font-weight:400}
.search-card .rule{position:absolute;left:19px;right:19px;top:54px}
.user-field{position:absolute;left:22px;top:82px;width:506px;height:23px;border-radius:12px;background:#1b1d22;display:flex;align-items:center;font-size:9px;color:var(--dim)}
.user-field .ucirc{width:23px;height:23px;border-radius:50%;background:var(--accent);display:flex;align-items:center;justify-content:center;margin-right:6px;color:#fff}
.search-btn{position:absolute;right:0;top:0;height:23px;width:76px;border-radius:12px;background:var(--accent);color:#fff;font-size:9px;display:flex;align-items:center;justify-content:center;gap:5px}

/* panel 4 */
.trucker-card{left:97px;top:90px;width:733px;height:148px}
.trucker-card .avatar{left:30px;top:8px;width:104px;height:104px}
.trucker-card .pname{left:0;width:163px;top:121px}
.trucker-card .vline{position:absolute;left:164px;top:14px;width:1px;height:120px;background:#3a3d44}
.trucker-card .minus{position:absolute;right:20px;top:18px;width:10px;height:1.5px;background:var(--text)}
.tstat{position:absolute;font-size:6.5px;display:flex;align-items:center;width:180px}
.tstat .lab{display:flex;align-items:center;gap:4px;width:95px}
.tstat .lab svg{width:8px;height:8px;color:var(--muted)}
.tstat .val{color:var(--dim)}
.jobs{position:absolute;left:97px;top:250px;width:733px;height:212px;overflow:hidden;border:1px solid #1f2126;border-radius:12px;background:rgba(10,11,14,.55)}
.job{position:absolute;width:169px;height:171px;border-radius:10px;background:#17181c;border:1px solid #24262b;font-size:7px}
.job.active{background:var(--accent);border-color:var(--accent)}
.job h3{position:absolute;left:14px;top:10px;font-size:8px;font-weight:700}
.job .sep{position:absolute;left:0;right:0;top:28px;height:1px;background:#2b2e34}
.job.active .sep{background:#5cc3ec}
.job .dt{position:absolute;left:14px;right:14px;top:36px;display:flex;justify-content:space-between;color:#c8ccd2}
.job .dt small{display:block;font-size:5px;color:var(--dim)}
.job .dt div:last-child{text-align:right}
.job.active .dt,.job.active .dt small,.job.active .place{color:#e8f6fd}
.job .place{position:absolute;left:14px;display:flex;gap:4px;color:#c8ccd2;line-height:11px}
.job .place svg{width:7px;height:7px;margin-top:2px;flex:none}
.job .foot{position:absolute;left:14px;right:14px;top:148px;display:flex;justify-content:space-between;font-size:7.5px}
.job .foot span{display:flex;align-items:center;gap:3px}
.job .foot svg{width:8px;height:8px}
</style>
</head>
<body>

<svg width="0" height="0" style="position:absolute">
  <defs>
    <symbol id="i-home" viewBox="0 0 12 12"><path d="M2 6 6 2.5 10 6V10.5H2Z" fill="none" stroke="currentColor" stroke-width="1.2"/></symbol>
    <symbol id="i-info" viewBox="0 0 12 12"><circle cx="6" cy="6" r="4.8" fill="none" stroke="currentColor" stroke-width="1.1"/><path d="M6 5.3V8.6M6 3.6v.6" stroke="currentColor" stroke-width="1.1"/></symbol>
    <symbol id="i-chev" viewBox="0 0 10 10"><path d="M2.5 4 5 6.5 7.5 4" fill="none" stroke="currentColor" stroke-width="1.2"/></symbol>
    <symbol id="i-clock" viewBox="0 0 10 10"><circle cx="5" cy="5" r="4" fill="none" stroke="currentColor" stroke-width="1"/><path d="M5 2.8V5l1.5 1" fill="none" stroke="currentColor" stroke-width="1"/></symbol>
    <symbol id="i-cup" viewBox="0 0 10 10"><path d="M3 1.5h4v3a2 2 0 0 1-4 0ZM5 6.5v1.5M3.2 8.5h3.6M3 2.5H1.5v1A1.5 1.5 0 0 0 3 5M7 2.5h1.5v1A1.5 1.5 0 0 1 7 5" fill="none" stroke="currentColor" stroke-width=".9"/></symbol>
    <symbol id="i-search" viewBox="0 0 10 10"><circle cx="4.3" cy="4.3" r="3" fill="none" stroke="currentColor" stroke-width="1.1"/><path d="M6.5 6.5 9 9" stroke="currentColor" stroke-width="1.1"/></symbol>
    <symbol id="i-user" viewBox="0 0 10 10"><circle cx="5" cy="3.5" r="2" fill="none" stroke="currentColor" stroke-width="1"/><path d="M1.5 9a3.5 3.5 0 0 1 7 0" fill="none" stroke="currentColor" stroke-width="1"/></symbol>
    <symbol id="i-pin" viewBox="0 0 10 10"><path d="M5 9S2 6 2 4a3 3 0 0 1 6 0c0 2-3 5-3 5Z" fill="none" stroke="currentColor" stroke-width="1"/><circle cx="5" cy="4" r="1" fill="currentColor"/></symbol>
    <symbol id="i-flag" viewBox="0 0 10 10"><path d="M2 9V1.5h6l-1.5 2 1.5 2H2" fill="none" stroke="currentColor" stroke-width="1"/></symbol>
    <symbol id="i-road" viewBox="0 0 10 10"><path d="M3 1 1.5 9M7 1l1.5 8M5 1.5v1.5M5 4.5V6M5 7.5V9" fill="none" stroke="currentColor" stroke-width="1"/></symbol>
    <symbol id="i-box" viewBox="0 0 10 10"><rect x="1.5" y="2.5" width="7" height="6" rx="1" fill="none" stroke="currentColor" stroke-width="1"/><path d="M1.5 4.5h7" stroke="currentColor" stroke-width="1"/></symbol>
    <symbol id="i-cal" viewBox="0 0 10 10"><rect x="1.5" y="2" width="7" height="6.5" rx="1" fill="none" stroke="currentColor" stroke-width="1"/><path d="M1.5 4h7M3.5 1v2M6.5 1v2" stroke="currentColor" stroke-width="1"/></symbol>
    <symbol id="i-refresh" viewBox="0 0 10 10"><path d="M8.3 5A3.3 3.3 0 1 1 7 2.4M7.3 1v1.8H5.5" fill="none" stroke="currentColor" stroke-width="1"/></symbol>
    <symbol id="i-db" viewBox="0 0 10 10"><ellipse cx="5" cy="2.5" rx="3.5" ry="1.3" fill="none" stroke="currentColor" stroke-width="1"/><path d="M1.5 2.5v5c0 .7 1.6 1.3 3.5 1.3s3.5-.6 3.5-1.3v-5M1.5 5c0 .7 1.6 1.3 3.5 1.3S8.5 5.7 8.5 5" fill="none" stroke="currentColor" stroke-width="1"/></symbol>
    <symbol id="i-sort" viewBox="0 0 10 10"><path d="M1 3h4M1 5h3M1 7h2M7.5 8.5V1.5M6 3l1.5-1.5L9 3" fill="none" stroke="currentColor" stroke-width="1"/></symbol>
    <symbol id="i-filter" viewBox="0 0 10 10"><path d="M1.5 2h7L6 5.2V8.5L4 7.5V5.2Z" fill="none" stroke="currentColor" stroke-width="1"/></symbol>
    <symbol id="i-list" viewBox="0 0 10 10"><path d="M1.5 2.5h7M1.5 5h7M1.5 7.5h7" stroke="currentColor" stroke-width="1"/></symbol>
    <symbol id="i-truck" viewBox="0 0 10 10"><path d="M1 3h5v4H1ZM6 4.5h2l1 1.5v1H6" fill="none" stroke="currentColor" stroke-width="1"/><circle cx="2.8" cy="7.8" r=".8" fill="currentColor"/><circle cx="7.3" cy="7.8" r=".8" fill="currentColor"/></symbol>
    <symbol id="i-coin" viewBox="0 0 10 10"><circle cx="5" cy="5" r="3.8" fill="none" stroke="currentColor" stroke-width="1"/><path d="M5 2.8v4.4" stroke="currentColor" stroke-width="1"/></symbol>
  </defs>
</svg>

<!-- ===== Home screen ===== -->
<section class="panel" style="top:129px">
  <div class="scene art" role="img" aria-label="Dark jungle foliage backdrop in violet and teal" style="background:radial-gradient(ellipse 400px 200px at 50% 60%,#142a2a 0%,transparent 70%),linear-gradient(180deg,#1a1e2e 0%,#121a22 45%,#1d1530 100%)"></div>
  <header class="topbar">
    <div class="brand"><span class="brand-dot"></span><span class="brand-name">PlayTallyCollective</span></div>
    <nav class="nav">
      <span class="nav-item active" style="left:306px;color:var(--text)"><svg style="color:var(--accent)"><use href="#i-home"/></svg>Home</span>
      <span class="nav-item" style="left:372px"><span class="nav-dot"></span>Vaporn</span>
      <span class="nav-item" style="left:438px"><span class="nav-dot games"></span>Games<svg class="icon" style="width:8px"><use href="#i-chev"/></svg></span>
      <span class="nav-item" style="left:520px"><svg><use href="#i-info"/></svg>About us<svg class="icon" style="width:8px"><use href="#i-chev"/></svg></span>
      <span class="nav-line" style="left:296px"></span>
    </nav>
  </header>
  <div class="card hero-card">
    <h1 class="hero-title">PlayTallyCollective</h1>
    <div class="rule"></div>
    <h2 class="hero-sub">Welcome to the PlayTallyCollective!</h2>
    <div class="hero-text">
      <p>We offer you free and easy insights into your game statistics and achievements on multiple platforms and games.</p>
      <p>If you want to learn more about us visit our <a>about us</a> page, otherwise go ahead and try our service!</p>
      <p>This page is under constant construction and we are trying to add more stats, games and platforms over time, so stay tuned.</p>
    </div>
  </div>
  <div class="art" role="img" aria-label="Golden crown trophy illustration" style="left:99px;top:85px;width:64px;height:64px;border-radius:18px;background:radial-gradient(circle at 50% 55%,#f2c24a 0%,#c98b2c 60%,transparent 72%)"></div>
  <div class="art" role="img" aria-label="Cartoon king character figure" style="left:728px;top:315px;width:103px;height:130px;border-radius:40px;background:radial-gradient(ellipse at 50% 45%,#d9473c 0%,#9c2a2a 45%,rgba(40,20,30,0) 72%)"></div>
  <footer class="footbar"><span class="ver">Version: 7.7.0-e6c810c-113</span><span class="copy">© Talvorn.com Development</span><span class="imp">Imprint</span></footer>
</section>

<!-- ===== Platform profile screen ===== -->
<section class="panel" style="top:748px">
  <div class="scene art" role="img" aria-label="Dark jungle foliage backdrop in violet and teal" style="background:linear-gradient(180deg,#1a1d2b 0%,#121920 50%,#1c1530 100%)"></div>
  <header class="topbar">
    <div class="brand"><span class="brand-dot"></span><span class="brand-name">PlayTallyCollective</span></div>
    <nav class="nav">
      <span class="nav-item" style="left:306px"><svg><use href="#i-home"/></svg>Home</span>
      <span class="nav-item active" style="left:372px"><span class="nav-dot"></span>Vaporn</span>
      <span class="nav-item" style="left:438px"><span class="nav-dot games"></span>Games<svg class="icon" style="width:8px"><use href="#i-chev"/></svg></span>
      <span class="nav-item" style="left:520px"><svg><use href="#i-info"/></svg>About us<svg class="icon" style="width:8px"><use href="#i-chev"/></svg></span>
      <span class="nav-line" style="left:363px"></span>
    </nav>
    <div class="user-chip"><span class="face"></span>pixelornin<svg class="icon" style="width:8px"><use href="#i-chev"/></svg></div>
  </header>

  <div class="art" role="img" aria-label="Game character figure with twin pistols" style="left:17px;top:322px;width:84px;height:172px;border-radius:40px;background:linear-gradient(180deg,#3a3f48 0%,#1d2a34 60%,#12c2d4 62%,#1a1d24 70%,#101216 100%);opacity:.85"></div>
  <div class="art" role="img" aria-label="Game character figure in yellow hood" style="left:831px;top:306px;width:97px;height:188px;border-radius:40px 0 0 40px;background:linear-gradient(180deg,#d4a52a 0%,#8e6a2a 35%,#5b4a3a 70%,#2a2420 100%);opacity:.85"></div>

  <div class="card profile-card">
    <div class="tool-row">
      <svg><use href="#i-refresh"/></svg><svg><use href="#i-cal"/></svg><svg><use href="#i-coin"/></svg><svg><use href="#i-db"/></svg>
    </div>
    <div class="avatar" role="img" aria-label="Profile avatar illustration"></div>
    <div class="pname">pixelornin</div>
    <div class="badges">
      <span class="badge"><svg viewBox="0 0 20 20" stroke="#9a6de0"><path d="M10 1.5 17.4 5.8V14.2L10 18.5 2.6 14.2V5.8Z"/></svg>179</span>
      <span class="badge"><svg viewBox="0 0 20 20" stroke="#6b7fe8"><circle cx="10" cy="10" r="8.3"/></svg>15</span>
      <span class="badge"><svg viewBox="0 0 20 20" stroke="#e3b93a"><path d="M10 1.5 18.5 10 10 18.5 1.5 10Z"/></svg>87</span>
    </div>
    <div class="rule"></div>
    <div class="pstat" style="top:230px"><span class="lab">Played Games:</span><span class="val"><svg class="icon"><use href="#i-list"/></svg>1166 / 1644 (70%)</span></div>
    <div class="pstat" style="top:253px"><span class="lab">Total play time:</span><span class="val"><svg class="icon"><use href="#i-clock"/></svg>1 year 2 months...</span></div>
    <div class="pstat" style="top:276px"><span class="lab">Achievements:</span><span class="val"><svg class="icon"><use href="#i-box"/></svg>18007 / 63070 (28%)</span></div>
    <div class="pstat" style="top:299px"><span class="lab">Member since:</span><span class="val"><svg class="icon"><use href="#i-cal"/></svg>14.01.2009</span></div>
    <div class="pstat" style="top:322px"><span class="lab">Last played:</span><span class="val"><svg class="icon"><use href="#i-box"/></svg>Backdrop Studio</span></div>
    <div class="pstat" style="top:345px"><span class="lab">Last Update:</span><span class="val"><svg class="icon"><use href="#i-refresh"/></svg>27.12.2024 11:36h</span></div>
  </div>

  <div class="card stats-bar">
    <h2>User Statistics</h2>
    <svg class="plus" viewBox="0 0 16 16"><path d="M8 2v12M2 8h12"/></svg>
  </div>

  <div class="card games-card">
    <div class="search-pill"><svg class="icon"><use href="#i-search"/></svg>Search Game</div>
    <div class="select-pill">Achievement progress<svg class="icon" style="width:8px"><use href="#i-chev"/></svg></div>
    <div class="round-btn" style="left:498px"><svg class="icon" style="width:10px;height:10px"><use href="#i-sort"/></svg></div>
    <div class="round-btn" style="left:526px"><svg class="icon" style="width:10px;height:10px"><use href="#i-filter"/></svg></div>
    <div class="rule"></div>

    <div class="tile" style="left:19px;top:63px">
      <div class="cover" role="img" aria-label="Lunar Wish cover art" style="background:linear-gradient(90deg,#4b4f58,#8a8a7a 60%,#c79a3e)"></div>
      <div class="tile-meta"><span>Lunar Wish</span><span class="nums"><span><svg class="icon"><use href="#i-clock"/></svg>5h</span><span><svg class="icon"><use href="#i-cup"/></svg>1/1</span></span></div>
      <div class="bar">100%</div>
    </div>
    <div class="tile" style="left:194px;top:63px">
      <div class="cover" role="img" aria-label="Exit The Hall cover art" style="background:linear-gradient(90deg,#2a1414,#7a1f1f 50%,#2b2b2b)"></div>
      <div class="tile-meta"><span>Exit The Hall</span><span class="nums"><span><svg class="icon"><use href="#i-clock"/></svg>2h</span><span><svg class="icon"><use href="#i-cup"/></svg>3/3</span></span></div>
      <div class="bar">100%</div>
    </div>
    <div class="tile" style="left:368px;top:63px">
      <div class="cover" role="img" aria-label="Logic Loop cover art" style="background:linear-gradient(90deg,#3b2f8f,#6a4ad0 50%,#2f63c8)"></div>
      <div class="tile-meta"><span>Logic Loop</span><span class="nums"><span><svg class="icon"><use href="#i-clock"/></svg>27m</span><span><svg class="icon"><use href="#i-cup"/></svg>5/5</span></span></div>
      <div class="bar">100%</div>
    </div>

    <div class="tile" style="left:19px;top:168px">
      <div class="cover" role="img" aria-label="Rotten Manor 2 cover art" style="background:linear-gradient(90deg,#3b4a5e,#6b2626 60%,#1c1c1c)"></div>
      <div class="tile-meta"><span>Rotten Manor 2</span><span class="nums"><span><svg class="icon"><use href="#i-clock"/></svg>36m</span><span><svg class="icon"><use href="#i-cup"/></svg>6/6</span></span></div>
      <div class="bar">100%</div>
    </div>
    <div class="tile" style="left:194px;top:168px">
      <div class="cover" role="img" aria-label="Breakout 2091 cover art" style="background:linear-gradient(90deg,#2b2f36,#5a6068 50%,#a02828)"></div>
      <div class="tile-meta"><span>Breakout 2091</span><span class="nums"><span><svg class="icon"><use href="#i-clock"/></svg>43m</span><span><svg class="icon"><use href="#i-cup"/></svg>6/6</span></span></div>
      <div class="bar">100%</div>
    </div>
    <div class="tile" style="left:368px;top:168px">
      <div class="cover" role="img" aria-label="Tiny Realm cover art" style="background:linear-gradient(90deg,#7ab84a,#c8d07a 50%,#6fa8d8)"></div>
      <div class="tile-meta"><span>Tiny Realm</span><span class="nums"><span><svg class="icon"><use href="#i-clock"/></svg>5h</span><span><svg class="icon"><use href="#i-cup"/></svg>1/1</span></span></div>
      <div class="bar">100%</div>
    </div>

    <div class="tile" style="left:19px;top:270px"><div class="cover" role="img" aria-label="Twiggle Trail cover art" style="background:linear-gradient(90deg,#3aa0d8,#4cc04c)"></div></div>
    <div class="tile" style="left:194px;top:270px"><div class="cover" role="img" aria-label="Dwelling cover art" style="background:linear-gradient(90deg,#2a2c30,#55585e)"></div></div>
    <div class="tile" style="left:368px;top:270px"><div class="cover" role="img" aria-label="Visitors From Above cover art" style="background:linear-gradient(90deg,#3a4a7a,#c07a3a)"></div></div>
    <div class="fade"></div>
  </div>

  <footer class="footbar"><span class="ver">Version: 7.7.0-e6c810c-113</span><span class="copy">© Talvorn.com Development</span><span class="imp">Imprint</span></footer>
</section>

<!-- ===== User search screen ===== -->
<section class="panel" style="top:1370px">
  <div class="scene art" role="img" aria-label="Night city street scene with casino towers and traffic" style="background:radial-gradient(ellipse 300px 160px at 90px 170px,#5a3a8a 0%,transparent 70%),radial-gradient(ellipse 240px 200px at 840px 140px,#6a5a4a 0%,transparent 70%),linear-gradient(180deg,#1d2732 0%,#222a30 35%,#2c2822 60%,#14120f 100%)"></div>
  <header class="topbar">
    <div class="brand"><span class="brand-dot"></span><span class="brand-name">PlayTallyCollective</span></div>
    <nav class="nav">
      <span class="nav-item" style="left:306px"><svg><use href="#i-home"/></svg>Home</span>
      <span class="nav-item" style="left:372px"><span class="nav-dot"></span>Vaporn</span>
      <span class="nav-item active" style="left:438px"><span class="nav-dot games"></span>Games<svg class="icon" style="width:8px"><use href="#i-chev"/></svg></span>
      <span class="nav-item" style="left:520px"><svg><use href="#i-info"/></svg>About us<svg class="icon" style="width:8px"><use href="#i-chev"/></svg></span>
      <span class="nav-line" style="left:436px"></span>
    </nav>
    <div class="user-chip"><span class="face"></span>pixelornin<svg class="icon" style="width:8px"><use href="#i-chev"/></svg></div>
  </header>
  <div class="card search-card">
    <h2>Search Talvorn User</h2>
    <div class="rule"></div>
    <div class="user-field">
      <span class="ucirc"><svg class="icon" style="width:11px;height:11px"><use href="#i-user"/></svg></span>User Name
      <span class="search-btn"><svg class="icon" style="width:9px;height:9px"><use href="#i-search"/></svg>Search</span>
    </div>
  </div>
  <div class="art" role="img" aria-label="Violet magnifying glass illustration" style="left:686px;top:158px;width:88px;height:90px;border-radius:50%;background:radial-gradient(circle at 40% 40%,#2a2a3a 0%,#3a3060 35%,#a06ae0 50%,rgba(120,80,200,0) 66%)"></div>
  <footer class="footbar"><span class="ver">Version: 7.7.0-e6c810c-113</span><span class="copy">© Talvorn.com Development</span><span class="imp">Imprint</span></footer>
</section>

<!-- ===== Game profile screen ===== -->
<section class="panel" style="top:2003px">
  <div class="scene art" role="img" aria-label="Dimmed night city street scene" style="background:radial-gradient(ellipse 200px 220px at 60px 160px,#3a2a5a 0%,transparent 70%),radial-gradient(ellipse 200px 200px at 880px 170px,#3a342a 0%,transparent 70%),linear-gradient(180deg,#0d0f13 0%,#14161a 50%,#0c0c0e 100%)"></div>
  <header class="topbar">
    <div class="brand"><span class="brand-dot"></span><span class="brand-name">PlayTallyCollective</span></div>
    <nav class="nav">
      <span class="nav-item" style="left:306px"><svg><use href="#i-home"/></svg>Home</span>
      <span class="nav-item" style="left:372px"><span class="nav-dot"></span>Vaporn</span>
      <span class="nav-item active" style="left:438px"><span class="nav-dot games"></span>Games<svg class="icon" style="width:8px"><use href="#i-chev"/></svg></span>
      <span class="nav-item" style="left:520px"><svg><use href="#i-info"/></svg>About us<svg class="icon" style="width:8px"><use href="#i-chev"/></svg></span>
      <span class="nav-line" style="left:436px"></span>
    </nav>
    <div class="user-chip"><span class="face"></span>pixelornin<svg class="icon" style="width:8px"><use href="#i-chev"/></svg></div>
  </header>

  <div class="card trucker-card">
    <div class="avatar" role="img" aria-label="Profile avatar illustration"></div>
    <div class="pname">pixelornin</div>
    <div class="vline"></div>
    <div class="minus"></div>

    <div class="tstat" style="left:193px;top:27px"><span class="lab"><svg><use href="#i-box"/></svg>Jobs Completed</span><span class="val">140</span></div>
    <div class="tstat" style="left:193px;top:50px"><span class="lab"><svg><use href="#i-clock"/></svg>Total Time:</span><span class="val">2d 18h 58m</span></div>
    <div class="tstat" style="left:193px;top:73px"><span class="lab"><svg><use href="#i-road"/></svg>Total Distance:</span><span class="val">36.286,57mi</span></div>
    <div class="tstat" style="left:193px;top:96px"><span class="lab"><svg><use href="#i-coin"/></svg>Total Revenue:</span><span class="val">US$ 1.745.094</span></div>
    <div class="tstat" style="left:193px;top:119px"><span class="lab"><svg><use href="#i-coin"/></svg>Fines Paid:</span><span class="val">141</span></div>

    <div class="tstat" style="left:372px;top:27px"><span class="lab"><svg><use href="#i-flag"/></svg>Tollgates Passed:</span><span class="val">2</span></div>
    <div class="tstat" style="left:372px;top:50px"><span class="lab"><svg><use href="#i-truck"/></svg>Transportations used:</span><span class="val">0</span></div>
    <div class="tstat" style="left:372px;top:73px"><span class="lab"><svg><use href="#i-cup"/></svg>Total Experience:</span><span class="val">78685</span></div>
    <div class="tstat" style="left:372px;top:96px"><span class="lab"><svg><use href="#i-clock"/></svg>Total In-Game Time:</span><span class="val">66d 9h 46m</span></div>
    <div class="tstat" style="left:372px;top:119px"><span class="lab"><svg><use href="#i-box"/></svg>Total Mass:</span><span class="val">2674t</span></div>

    <div class="tstat" style="left:552px;top:27px"><span class="lab"><svg><use href="#i-truck"/></svg>Trucks driven:</span><span class="val">8</span></div>
    <div class="tstat" style="left:552px;top:50px"><span class="lab"><svg><use href="#i-coin"/></svg>Total fines:</span><span class="val">US$ 118.660</span></div>
    <div class="tstat" style="left:552px;top:73px"><span class="lab"><svg><use href="#i-coin"/></svg>Total toll paid:</span><span class="val">US$ 50</span></div>
    <div class="tstat" style="left:552px;top:96px"><span class="lab"><svg><use href="#i-box"/></svg>Paid for transportations:</span><span class="val">US$ 0</span></div>
  </div>

  <div class="jobs">
    <article class="job" style="left:11px;top:15px">
      <h3>Mountain Fun Gift Packs</h3><div class="sep"></div>
      <div class="dt"><div><small>Date</small>17.12.2023</div><div><small>Time</small>05:37</div></div>
      <div class="place" style="top:62px"><svg><use href="#i-pin"/></svg><span>Mountain Resort, Winterland<br>Snowy Peaks</span></div>
      <div class="place" style="top:93px"><svg><use href="#i-flag"/></svg><span>Ardmore,<br>Oklahoma Waldens</span></div>
      <div class="foot"><span><svg><use href="#i-clock"/></svg>17m</span><span><svg><use href="#i-road"/></svg>101,9mi</span><span><svg><use href="#i-box"/></svg>19t</span></div>
    </article>
    <article class="job active" style="left:192px;top:15px">
      <h3>Christmas Handmade Gifts</h3><div class="sep"></div>
      <div class="dt"><div><small>Date</small>17.12.2023</div><div><small>Time</small>05:21</div></div>
      <div class="place" style="top:62px"><svg><use href="#i-pin"/></svg><span>Corpus Christi,Texas<br>Home Store</span></div>
      <div class="place" style="top:93px"><svg><use href="#i-flag"/></svg><span>Town Square, Winterland<br>Christmas Market</span></div>
      <div class="foot"><span><svg><use href="#i-clock"/></svg>14m</span><span><svg><use href="#i-road"/></svg>73,32mi</span><span><svg><use href="#i-box"/></svg>19t</span></div>
    </article>
    <article class="job" style="left:373px;top:15px">
      <h3>Bulldozer</h3><div class="sep"></div>
      <div class="dt"><div><small>Date</small>28.05.2023</div><div><small>Time</small>20:37</div></div>
      <div class="place" style="top:62px"><svg><use href="#i-pin"/></svg><span>Laredo, Texas<br>Deep Wells</span></div>
      <div class="place" style="top:93px"><svg><use href="#i-flag"/></svg><span>Corpus Christi, Texas<br>Taylor Construction Group</span></div>
      <div class="foot"><span><svg><use href="#i-clock"/></svg>23m</span><span><svg><use href="#i-road"/></svg>240,47mi</span><span><svg><use href="#i-box"/></svg>18t</span></div>
    </article>
    <article class="job" style="left:554px;top:15px">
      <h3>Home Accessories</h3><div class="sep"></div>
      <div class="dt"><div><small>Date</small>28.05.2023</div><div><small>Time</small>19:15</div></div>
      <div class="place" style="top:62px"><svg><use href="#i-pin"/></svg><span>Brownsville,<br>Texas Plugged</span></div>
      <div class="place" style="top:93px"><svg><use href="#i-flag"/></svg><span>Laredo, Texas<br>GARC</span></div>
      <div class="foot"><span><svg><use href="#i-clock"/></svg>24m</span><span><svg><use href="#i-road"/></svg>223,07mi</span><span><svg><use href="#i-box"/></svg>19t</span></div>
    </article>
    <article class="job" style="left:11px;top:193px"><h3>Ridgeline Trucks</h3></article>
    <article class="job" style="left:192px;top:193px"><h3>Forklifts</h3></article>
    <article class="job" style="left:373px;top:193px"><h3>Empty Pallets</h3></article>
    <article class="job" style="left:554px;top:193px"><h3>Lift Truck Chassis</h3></article>
  </div>

  <footer class="footbar"><span class="ver">Version: 7.7.0-e6c810c-113</span><span class="copy">© Talvorn.com Development</span><span class="imp">Imprint</span></footer>
</section>

</body>
</html>
```